Luxury modern loose tea company web design

I am a high-end modern luxury loose leaf tea business. I have a website domain that is hosted on Shopify. I’m looking for designers that have a modern flair and are able to create websites that would easily attract major YouTube and Snapgrid influencers as well as a modern millennial.

Luxury is at the fore front of the design scheme and branding and should be incorporated in ALL aspects of the website. As well if designers are able to implement any unique features to make the shopping experience more fun and memorable that is a major bonus. The main colors I work with are black, silver and gold, once again reinforcing the luxury feel.

My brand is called Sip of Lume

Target Market(s)

The Modern Millenial, 21-40 (bullseye 28). He or she is a young professional that has a disposable income in which they do like to indulge with. They balance their demanding work schedules well and they have a work hard/play hard mindset. This professional is more likely to order their daily coffee from Brewvant as opposed to Ned Kallory and their social media profiles are a big indicator as to their hobbies and lifestyles outside of their work environment. They enjoy shopping at stores like Vexa, Halcyne, UrbanLoom/UrbanGent and for special occasions are willing to splurge at stores like Marlowe's, Hall Verdine and… They live a pretty active lifestyle and are highly influenced by social media trending products

Colors

Designer to choose colors to be used in the design.

Requirements
Must have
• luxury feel
• unique customer experience

```html
<!DOCTYPE html>
<html lang="en">
<head>
<meta charset="utf-8">
<title>Sip of Lume — Luxury Loose Leaf Tea</title>
<link href="https://fonts.googleapis.com/css2?family=Marcellus&family=Open+Sans:wght@400;600;700&display=swap" rel="stylesheet">
<style>
:root{
  --gold:#c8912a;
  --ink:#1b1b1b;
  --text:#555555;
  --muted:#8a8a8a;
  --paper:#ffffff;
  --soft:#f7f7f7;
  --cream:#fcf7e8;
  --footer:#0d0d0d;
  --footer-text:#cfcfcf;
}
*{margin:0;padding:0;box-sizing:border-box}
html,body{width:1200px;height:4358px;overflow:hidden}
body{position:relative;background:var(--paper);font-family:"Open Sans",sans-serif;color:var(--text)}
h1,h2,h4{font-weight:400}
.abs{position:absolute}

/* hero */
.hero{left:0;top:0;width:1200px;height:628px;background:linear-gradient(160deg,#8c7a68 0%,#5e4c3c 40%,#a99a88 70%,#4b3a2b 100%)}
.brand{left:96px;top:42px;font-family:"Marcellus",serif;font-size:40px;color:#fff;letter-spacing:1px}
.nav{top:60px;left:453px;display:flex;gap:38px;font-family:"Marcellus",serif;font-size:18px;color:#fff;letter-spacing:.5px}
.nav-icon{top:51px;width:40px;height:40px;border-radius:50%;display:flex;align-items:center;justify-content:center}
.nav-search{left:1002px;border:2px solid #fff}
.nav-cart{left:1058px;background:var(--gold)}
.hero-title{left:0;width:1200px;top:380px;text-align:center;font-family:"Marcellus",serif;font-size:54px;line-height:68px;color:#fff;letter-spacing:2px}
.dots{top:563px;left:570px;display:flex;gap:6px}
.dots span{width:12px;height:12px;border-radius:50%;border:2px solid #fff}
.dots span.on{background:#fff}

/* headings */
.section-title{left:0;width:1200px;text-align:center;font-family:"Marcellus",serif;font-size:52px;color:var(--ink);letter-spacing:1px}

.story-text{left:232px;width:736px;top:790px;text-align:center;font-size:13.5px;line-height:24px;color:var(--text)}

/* products */
.products{left:0;top:947px;width:1200px;height:1511px;background:var(--soft)}
.card{background:var(--cream);display:flex;align-items:center;justify-content:center}
.shot{border-radius:4px}
.label{font-size:23px;color:var(--ink);text-align:center}
.label b{font-weight:700}

/* newsletter */
.news{left:0;top:2458px;width:1200px;height:383px;background:linear-gradient(100deg,#5a3a20 0%,#2c1d12 35%,#3b2818 60%,#7a4a1c 100%)}
.news-title{left:0;width:1200px;top:2540px;text-align:center;font-family:"Marcellus",serif;font-size:48px;color:#fff;letter-spacing:2px}
.news-sub{left:0;width:1200px;top:2620px;text-align:center;font-size:17px;color:#eee}
.news-input{left:302px;top:2687px;width:450px;height:55px;background:#fff;font-size:15px;color:#444;padding:18px 26px}
.news-btn{left:752px;top:2687px;width:143px;height:55px;background:var(--gold);color:#fff;font-size:15px;font-weight:700;display:flex;align-items:center;justify-content:center;letter-spacing:.5px}

/* blog */
.post-title{font-size:22px;font-weight:600;line-height:34px;color:var(--ink);white-space:nowrap}
.post-meta{font-size:14px;color:var(--text);display:flex;align-items:center;gap:8px}
.post-meta i{color:var(--gold);font-style:normal}
.post-text{font-size:14px;line-height:24px;color:var(--text)}
.btn{width:131px;height:46px;border-radius:23px;background:var(--gold);color:#fff;font-size:13px;font-weight:700;display:flex;align-items:center;justify-content:center;letter-spacing:.5px}
.photo{border-radius:2px}

/* footer */
.footer{left:0;top:3951px;width:1200px;height:407px;background:var(--footer)}
.f-head{top:4015px;font-family:"Marcellus",serif;font-size:19px;color:#fff;letter-spacing:1px}
.f-list{top:4060px;list-style:none;font-size:13px;line-height:27.6px;color:var(--footer-text)}
.f-social{left:526px;top:4052px;list-style:none;font-size:13px;color:var(--footer-text)}
.f-social li{display:flex;align-items:center;gap:22px;height:44px}
.f-social span.dot{width:34px;height:34px;border-radius:50%;border:1.5px solid #888;display:flex;align-items:center;justify-content:center}
.f-about{left:767px;top:4058px;width:330px;font-size:13px;line-height:21px;color:var(--footer-text)}
.copy{left:99px;top:4287px;font-size:13px;color:var(--footer-text)}
.pay{top:4282px;display:flex;gap:8px;left:872px}
.pay span{width:50px;height:26px;border-radius:3px;background:#bdbdbd}
</style>
</head>
<body>

<header>
  <div class="abs hero" role="img" aria-label="Tea being poured from a white teapot into a white cup on a saucer, with fresh tea leaves beside it"></div>
  <div class="abs brand">Sip of Lume</div>
  <nav class="abs nav"><span>ORDER ONLINE</span><span>ABOUT US</span><span>BLOG</span><span>CONTACT US</span></nav>
  <div class="abs nav-icon nav-search">
    <svg width="18" height="18" viewBox="0 0 18 18"><circle cx="7.5" cy="7.5" r="5.5" fill="none" stroke="#fff" stroke-width="2"/><line x1="11.5" y1="11.5" x2="16" y2="16" stroke="#fff" stroke-width="2"/></svg>
  </div>
  <div class="abs nav-icon nav-cart">
    <svg width="18" height="18" viewBox="0 0 18 18"><path d="M1 2h3l2 9h9l2-6H5" fill="none" stroke="#fff" stroke-width="1.8"/><circle cx="7" cy="15" r="1.5" fill="#fff"/><circle cx="14" cy="15" r="1.5" fill="#fff"/></svg>
  </div>
  <h1 class="abs hero-title">LUXURY LOOSE LEAF<br>TEA BUSINESS</h1>
  <div class="abs dots"><span class="on"></span><span></span><span></span><span></span></div>
</header>

<section>
  <h2 class="abs section-title" style="top:708px">OUR STORY</h2>
  <p class="abs story-text">Nemo enim ipsam voluptatem quia voluptas sit aspernatur aut odit aut fugit, sed quia consequuntur magni dolores eos qui ratione voluptatem sequi nesciunt neque porro quisquam est, qui dolorem ipsum quia dolor sit amet, consectetur adipisci velit, sed quia non numquam eius modi tempora incidunt ut labore et quis nostrum exercitat.</p>
</section>

<section>
  <div class="abs products"></div>
  <h2 class="abs section-title" style="top:1025px">FEATURED PRODUCTS</h2>

  <div class="abs card" style="left:96px;top:1156px;width:581px;height:480px"><div class="shot" role="img" aria-label="Black gift box of loose leaf tea with a white leaf pattern" style="width:380px;height:280px;background:linear-gradient(150deg,#2a2a2a,#0c0c0c)"></div></div>
  <div class="abs label" style="left:96px;top:1662px;width:581px">Finibus Bonoet Maloru - <b>$28</b></div>

  <div class="abs card" style="left:715px;top:1156px;width:383px;height:189px"><div class="shot" role="img" aria-label="Wooden bowl of dark loose tea with green leaves" style="width:210px;height:120px;background:radial-gradient(ellipse,#8a6a3e 0%,#c59a5a 55%,#fcf7e8 75%)"></div></div>
  <div class="abs label" style="left:715px;top:1379px;width:383px">Finibus Bonoet Maloru - <b>$28</b></div>

  <div class="abs card" style="left:715px;top:1444px;width:383px;height:192px"><div class="shot" role="img" aria-label="Wooden scoop over a pile of green loose leaf tea" style="width:250px;height:130px;background:radial-gradient(ellipse,#5a6a2e 0%,#7f8c46 50%,#fcf7e8 75%)"></div></div>
  <div class="abs label" style="left:715px;top:1662px;width:383px">Finibus Bonoet Maloru - <b>$28</b></div>

  <div class="abs card" style="left:96px;top:1790px;width:386px;height:186px"><div class="shot" role="img" aria-label="Cast iron teapot beside scattered black tea" style="width:250px;height:130px;background:radial-gradient(ellipse,#3a3836 0%,#6a625a 50%,#fcf7e8 75%)"></div></div>
  <div class="abs label" style="left:96px;top:2011px;width:386px">Finibus Bonoet Maloru - <b>$28</b></div>

  <div class="abs card" style="left:96px;top:2077px;width:386px;height:192px"><div class="shot" role="img" aria-label="Green tea tin tipped over with black tea spilling out" style="width:270px;height:130px;background:radial-gradient(ellipse,#2f5a3a 0%,#5e5440 50%,#fcf7e8 75%)"></div></div>
  <div class="abs label" style="left:96px;top:2298px;width:386px">Finibus Bonoet Maloru - <b>$28</b></div>

  <div class="abs card" style="left:517px;top:1790px;width:581px;height:479px"><div class="shot" role="img" aria-label="Black flat tea box shown at an angle with white leaf pattern" style="width:300px;height:340px;background:linear-gradient(150deg,#2a2a2a,#0a0a0a);transform:rotate(18deg)"></div></div>
  <div class="abs label" style="left:517px;top:2298px;width:581px">Finibus Bonoet Maloru - <b>$28</b></div>
</section>

<section>
  <div class="abs news" role="img" aria-label="Tea being poured into a glass cup in warm amber light"></div>
  <h2 class="abs news-title">SUBSCRIBE TO OUR NEWSLETTER</h2>
  <p class="abs news-sub">Sign up to stay in the loop. Receive updates, access to exclusive deals, and more.</p>
  <div class="abs news-input">Email Address</div>
  <div class="abs news-btn">SUBSCRIBE</div>
</section>

<section>
  <h2 class="abs section-title" style="top:2930px">FROM THE BLOG</h2>

  <article>
    <h3 class="abs post-title" style="left:96px;top:3084px">Sed ut perspiciatis unde omnis issnatus<br>sivol uptatem accusantium dolore</h3>
    <div class="abs post-meta" style="left:96px;top:3171px"><i>&#9635;</i> 10/09/2018 &nbsp;| &nbsp;<i>&#9679;</i> John Doe</div>
    <p class="abs post-text" style="left:96px;top:3210px;width:450px">Nemo enim ipsam voluptatem quia voluptas sit aspernatur aut odut fugit, sed quia consequuntur magni dolores eos qui ratione voluptatem sequi nesciun ue porro quisquam est, qui dolorem ipsum quia dolor sit amet, consectetur, adipisci velit, sed quia</p>
    <div class="abs btn" style="left:96px;top:3344px">READ MORE</div>
    <div class="abs photo" role="img" aria-label="White teacups and scattered dark tea leaves on a wooden table by a window" style="left:598px;top:3059px;width:500px;height:360px;background:linear-gradient(135deg,#b7aa96,#6a5a48 60%,#2e261e)"></div>
  </article>

  <article>
    <div class="abs photo" role="img" aria-label="Wooden spoon of black loose tea beside a glass of tea" style="left:96px;top:3489px;width:502px;height:360px;background:linear-gradient(135deg,#3a2618,#6a5a4a 55%,#9a9086)"></div>
    <h3 class="abs post-title" style="left:660px;top:3514px">Sed ut perspiciatis unde omnis issnatus<br>sivol uptatem accusantium dolore</h3>
    <div class="abs post-meta" style="left:660px;top:3601px"><i>&#9635;</i> 10/09/2018 &nbsp;| &nbsp;<i>&#9679;</i> John Doe</div>
    <p class="abs post-text" style="left:660px;top:3638px;width:440px">Nemo enim ipsam voluptatem quia voluptas sit aspernatur aut odut fugit, sed quia consequuntur magni dolores eos qui ratione voluptatem sequi nesciun ue porro quisquam est, qui dolorem ipsum quia dolor sit amet, consectetur, adipisci velit, sed quia</p>
    <div class="abs btn" style="left:660px;top:3771px">READ MORE</div>
  </article>
</section>

<footer>
  <div class="abs footer"></div>
  <h4 class="abs f-head" style="left:99px">INFORMATION</h4>
  <ul class="abs f-list" style="left:99px"><li>About Us</li><li>Careers</li><li>Privacy &amp; Security</li><li>Site Map</li><li>Terms of Use</li><li>Blog</li></ul>
  <h4 class="abs f-head" style="left:290px">HELP &amp; SUPPORT</h4>
  <ul class="abs f-list" style="left:290px"><li>Recommended Reading</li><li>Submit your Story</li><li>Contact Us</li><li>FAQ</li><li>How to Order</li></ul>
  <h4 class="abs f-head" style="left:526px">STAY CONNECTED</h4>
  <ul class="abs f-social">
    <li><span class="dot"></span>Friendwall</li>
    <li><span class="dot"></span>Snapgrid</li>
    <li><span class="dot"><svg width="14" height="10" viewBox="0 0 14 10"><rect x="0.5" y="0.5" width="13" height="9" fill="none" stroke="#ddd"/><path d="M0.5 0.5L7 6l6.5-5.5" fill="none" stroke="#ddd"/></svg></span>Email</li>
    <li><span class="dot"></span>Workline</li>
  </ul>
  <h4 class="abs f-head" style="left:767px">ABOUT</h4>
  <p class="abs f-about">At vero eos et accusamus et iusto odio dignissimos ducimus qui blanditiis praesentium voluptatum deleniti atque corrupti quos dolores et quas molestias excepturi sint occaecati cupiditate non provident, similique sunt in culpa qui officia deserunt.</p>
  <p class="abs copy">Copyrights © 2018, Sip of Lume. All Rights Reserved.</p>
  <div class="abs pay"><span></span><span></span><span></span><span></span><span></span></div>
</footer>

</body>
</html>
```